We need a new business card that reflects who we are. Professional, classy, modern, and service ori

We need a business card design for a window coverings design company in Kansas City called Bright Lane Interiors. We offer professional, modern, and high quality window covering products. We are looking to portray an image of a big, national franchise. We are a 5 location (with showrooms) business with 10 professional designers and 4 professional installers. These cards will be used with Thank you cards, given to realtors, and asked for referrals with.

Target Market(s)

Kansas City

Industry/Entity Type

Business

Contact Information for Business Card

We would like our card to look clean and simple on the front, featuring our logo and Marlow Fenwick's. Our designers' phone numbers and emails should be displayed as well as their title.

Font styles to use
Sans Serif

Colors

Designer to choose colors to be used in the design.

Requirements
Must have
• Front - Logos, name, phone number, email address
• Back - Showroom locations, social media? Appt date/time?
Nice to have
• I would like a clean and modern look (not contemporary. I like a white background, but I am open to ideas. Looking for a "National chain" look for a small business.
Should not have
• Too much busyness.

```html
<!DOCTYPE html>
<html lang="en">
<head>
<meta charset="utf-8">
<title>Bright Lane Interiors – Business Card</title>
<link rel="stylesheet" href="https://fonts.googleapis.com/css2?family=Roboto:wght@400;500;700&family=Roboto+Condensed:wght@500;700&family=Marcellus&family=EB+Garamond:wght@400&display=swap">
<style>
  :root {
    --backdrop: #2b2b2b;
    --paper: #f3f3f3;
    --accent: #c5383d;
    --ink: #111111;
    --slate: #8e9194;
    --text-grey: #55585b;
    --rule: #9a9a9a;
    --white: #ffffff;
    --gallery-mark: #f28a1d;
  }
  * { margin: 0; padding: 0; box-sizing: border-box; }
  html, body { width: 1200px; height: 960px; overflow: hidden; }
  body { background: var(--backdrop); position: relative; font-family: "Roboto", Arial, sans-serif; }

  .card {
    position: absolute;
    width: 600px;
    height: 343px;
    background: var(--paper);
    box-shadow: 0 3px 8px rgba(0,0,0,.45);
  }
  .card--front { left: 314px; top: 113px; }
  .card--back { left: 311px; top: 472px; }

  /* Front */
  .person { position: absolute; right: 42px; top: 46px; text-align: right; }
  .person__name { font-family: "Roboto Condensed", Arial, sans-serif; font-weight: 700; font-size: 23px; color: var(--accent); line-height: 1; }
  .person__title { font-family: "Roboto Condensed", Arial, sans-serif; font-weight: 700; font-size: 15px; color: var(--ink); margin-top: 5px; letter-spacing: .3px; }
  .person-rule { position: absolute; left: 39px; right: 42px; top: 96px; height: 1px; background: var(--rule); }

  .wordmark { font-family: "Marcellus", Georgia, serif; color: var(--ink); line-height: 1; white-space: nowrap; }
  .tagline { font-family: "EB Garamond", Georgia, serif; color: var(--ink); white-space: nowrap; }

  .card--front .wordmark { position: absolute; left: 35px; top: 148px; font-size: 34px; }
  .card--front .tagline { position: absolute; left: 36px; top: 185px; font-size: 19px; }

  .contact-band {
    position: absolute; left: 0; top: 243px; width: 558px; height: 54px;
    background: var(--slate); display: flex; align-items: center; color: var(--white);
  }
  .contact-band__phone { font-size: 21px; padding-left: 35px; padding-right: 10px; letter-spacing: .3px; }
  .contact-band__divider { width: 1px; height: 34px; background: var(--white); margin-right: 10px; }
  .contact-band__web { font-size: 14.5px; line-height: 19px; }

  .monogram { position: absolute; display: flex; align-items: center; gap: 8px; }
  .monogram__square { width: 30px; height: 30px; background: var(--accent); }
  .monogram__letters { font-family: "Marcellus", Georgia, serif; font-size: 54px; line-height: 1; color: var(--ink); letter-spacing: 2px; }
  .card--front .monogram { left: 420px; top: 240px; }

  /* Back */
  .card--back .monogram { left: 100px; top: 70px; }
  .card--back .wordmark { position: absolute; left: 54px; top: 136px; font-size: 23px; }
  .card--back .tagline { position: absolute; left: 54px; top: 160px; font-size: 12.5px; }

  .locations { position: absolute; right: 53px; top: 43px; text-align: right; font-size: 14px; line-height: 18px; color: var(--text-grey); font-weight: 500; }
  .locations__heading { color: var(--accent); font-weight: 700; }
  .locations__list { list-style: none; }

  .gallery { position: absolute; right: 53px; top: 156px; display: flex; align-items: center; gap: 5px; font-size: 12.5px; font-weight: 700; color: var(--text-grey); }
  .gallery__mark { width: 16px; height: 16px; border-radius: 50%; background: var(--gallery-mark); }

  .social { position: absolute; right: 53px; top: 185px; display: flex; gap: 3px; }
  .social__dot { width: 17px; height: 17px; border-radius: 50%; background: var(--accent); }

  .appointment { position: absolute; left: 52px; color: var(--accent); font-size: 16px; display: flex; align-items: baseline; }
  .appointment--name { top: 237px; right: 53px; }
  .appointment--when { top: 278px; right: 49px; }
  .appointment__leader { flex: 1; border-bottom: 1.5px dotted #6a6a6a; margin: 0 3px; transform: translateY(-3px); }
  .appointment__leader--date { flex: 0 0 212px; }
  .appointment__suffix { font-size: 12px; margin-left: 4px; }
</style>
</head>
<body>

<section class="card card--front" aria-label="Card front">
  <div class="person">
    <p class="person__name">DANA WHITLOW</p>
    <p class="person__title">DESIGNER</p>
  </div>
  <div class="person-rule"></div>

  <p class="wordmark">Bright Lane Interiors</p>
  <p class="tagline">Window Fashions, Custom Shades &amp; Home Accents</p>

  <div class="contact-band">
    <span class="contact-band__phone">913.555.0148</span>
    <span class="contact-band__divider"></span>
    <span class="contact-band__web">info@brightlaneinteriors.com<br>brightlaneinteriors.com</span>
  </div>

  <div class="monogram">
    <span class="monogram__square"></span>
    <span class="monogram__letters">BLI</span>
  </div>
</section>

<section class="card card--back" aria-label="Card back">
  <div class="monogram">
    <span class="monogram__square"></span>
    <span class="monogram__letters">BLI</span>
  </div>
  <p class="wordmark">Bright Lane Interiors</p>
  <p class="tagline">Window Fashions, Custom Shades &amp; Home Accents</p>

  <div class="locations">
    <p class="locations__heading">SHOWROOM LOCATIONS</p>
    <ul class="locations__list">
      <li>MAPLE RIDGE</li>
      <li>CEDAR HOLLOW</li>
      <li>WESTBROOK</li>
      <li>NORTH FALLS</li>
      <li>BIRCHWOOD</li>
    </ul>
  </div>

  <div class="gallery">
    <span>Marlow Fenwick Gallery</span>
    <span class="gallery__mark"></span>
  </div>

  <div class="social" aria-label="Social media">
    <span class="social__dot"></span>
    <span class="social__dot"></span>
    <span class="social__dot"></span>
    <span class="social__dot"></span>
  </div>

  <div class="appointment appointment--name">
    <span>Name :</span><span class="appointment__leader"></span>
  </div>
  <div class="appointment appointment--when">
    <span>Date :</span><span class="appointment__leader appointment__leader--date"></span>
    <span>Time :</span><span class="appointment__leader"></span>
    <span class="appointment__suffix">AM/PM</span>
  </div>
</section>

</body>
</html>
```